Business Card Design for Marketing Firm

Looking for business card design for higher end marketing firm. Clean but impressionable/trendy. We are a marketing firm that represents manufacturers in the foodservice equipment and supply industry. Our customers are end users such has hotels, restaurants, country clubs, convention centers and casinos as well as distributors of restaurants supplies and equipment, and manufacturers of foodservice equipment and supplies.
Target Market(s)
Hotels, Restaurants, Supply & Equipment Distributors, Foodservice Manufacturers
Industry/Entity Type
Foodservice/Hospitality
Contact Information for Business Card
Name, Title, Contact Number, Email, Website, Social Media, Address
Requirements
Must have
- Clean & Simple but Serious and Impressionable

```html
<!DOCTYPE html>
<html lang="en">
<head>
<meta charset="utf-8">
<title>Meridian Foodservice Reps — Business Card</title>
<link rel="stylesheet" href="https://fonts.googleapis.com/css2?family=Cinzel:wght@600&family=EB+Garamond:wght@400&display=swap">
<style>
  :root {
    --backdrop: #8f8f8f;
    --paper: #ffffff;
    --navy: #00007d;
    --ink: #3c3c3c;
    --rule: #222222;
  }
  * { margin: 0; padding: 0; box-sizing: border-box; }
  html, body {
    width: 1200px; height: 1200px; overflow: hidden;
    background: var(--backdrop);
  }
  .card {
    position: absolute;
    left: 250px;
    width: 700px; height: 400px;
    border-radius: 18px;
    overflow: hidden;
  }
  .card--front { top: 170px; background: var(--paper); }
  .card--back  { top: 631px; background: var(--navy); }

  .brand-name {
    font-family: "Cinzel", "Times New Roman", serif;
    font-weight: 600;
    letter-spacing: 0.02em;
    line-height: 1.15;
  }
  .card--front .brand-name {
    position: absolute; right: 35px; top: 80px;
    text-align: right; font-size: 22px; color: var(--navy);
  }
  .brand-dot {
    display: inline-block; width: 10px; height: 10px;
    border-radius: 50%; background: currentColor;
    margin-right: 8px; vertical-align: 3px;
  }
  .holder-name {
    position: absolute; left: 33px; top: 208px;
    font-family: "Cinzel", "Times New Roman", serif;
    font-weight: 600; font-size: 27px; letter-spacing: 0.04em;
    color: var(--navy);
  }
  .holder-title {
    position: absolute; left: 33px; top: 244px;
    font-family: "EB Garamond", Georgia, serif;
    font-size: 19px; letter-spacing: 0.03em; color: var(--ink);
  }
  .divider {
    position: absolute; left: 35px; right: 35px; top: 280px;
    height: 1px; background: var(--rule);
  }
  .contact-list {
    position: absolute; left: 35px; top: 292px;
    list-style: none;
    font-family: "EB Garamond", Georgia, serif;
    font-size: 17px; color: var(--ink);
  }
  .contact-list li { display: flex; align-items: center; height: 25px; }
  .contact-list li:first-child { font-size: 19px; }
  .contact-list svg { width: 13px; height: 13px; margin-right: 13px; fill: var(--navy); }
  .office-address {
    position: absolute; right: 35px; top: 292px;
    text-align: right; font-style: normal;
    font-family: "EB Garamond", Georgia, serif;
    font-size: 17px; line-height: 25px; color: var(--ink);
  }
  .office-address .office-name { color: var(--navy); }

  .card--back .brand-name {
    position: absolute; left: 0; right: 0; top: 150px;
    text-align: center; font-size: 38px; color: var(--paper);
  }
</style>
</head>
<body>
  <section class="card card--front">
    <div class="brand-name"><span class="brand-dot"></span>Meridian Foodservice<br>Reps</div>

    <h1 class="holder-name">DANA WHITFIELD</h1>
    <p class="holder-title">Founder &amp; CEO</p>
    <div class="divider"></div>

    <ul class="contact-list">
      <li>
        <svg viewBox="0 0 24 24" aria-hidden="true"><path d="M6.6 10.8a15.2 15.2 0 0 0 6.6 6.6l2.2-2.2c.3-.3.7-.4 1-.2 1.1.4 2.3.6 3.6.6.6 0 1 .4 1 1V20c0 .6-.4 1-1 1A17 17 0 0 1 3 4c0-.6.4-1 1-1h3.5c.6 0 1 .4 1 1 0 1.3.2 2.5.6 3.6.1.3 0 .7-.2 1z"/></svg>
        (555) 014-2297
      </li>
      <li>
        <svg viewBox="0 0 24 24" aria-hidden="true"><path d="M2 5h20v14H2z M3 6l9 7 9-7" stroke="#fff" stroke-width="1.5"/></svg>
        hello@meridianreps.com
      </li>
      <li>
        <svg viewBox="0 0 24 24" aria-hidden="true"><circle cx="12" cy="12" r="10"/><path d="M2 12h20M12 2c3 3 3 17 0 20M12 2c-3 3-3 17 0 20" stroke="#fff" stroke-width="1.5" fill="none"/></svg>
        meridianreps.com
      </li>
    </ul>

    <address class="office-address">
      <span class="office-name">Meridian Foodservice Reps</span><br>
      418 Orchard Lane<br>
      Hartwell, CT 06999
    </address>
  </section>

  <section class="card card--back">
    <div class="brand-name"><span class="brand-dot"></span>Meridian Foodservice<br>Reps</div>
  </section>
</body>
</html>
```